Redesign 2016 Digital Marketing Website and Convert to Wordpress

Technology needed to integrate:

- redesign and convert to wordpress
- gravity forms
- malware and hacker defense / honeypot (must be very secure from hackers)
- I want gravity forms to be a flow that asks many questions with icons and progress bar.
- 1 home page design
- 1 blog design
- 1 design for internal page content
- 1 multi step gravity form
I want to focus on SMB's. We are a marketing agency thats been around since 2016.

Site is: tallpine.agency

I am looking to redesign the homepage, blog page and services page. The services page will be a template for all inner pages of the site. All content needs to be moved into the new design.

I want to get ride of the weird video.

I need you to install gravity forms pro model so we can pass utms.

I need the gravity form to be a multi step form with icons.

All "contact us" or "get a free assesments" call to actions will go to this form only.

step 1:
what is your website

step 2:
what industry are you in
- option
- Home Services
- Legal
- Ecommerce
- Lead Gen

No matter which one they select its going to produce a differnt calculator for them.

Law:
How many leads did you get last month
how much is each ase worth on average
How much revenue do you want to make

Home servicse:
How many bookings did you get last month
How much is each service worht on average
How much revenue do you wangt to make

Ecommerce:
What is your average order value
How muny purchases did you have last month
How much revenue did you drive
How much revenue do you want to drive

For lead gen:
How many leads did you get lawt month
How much revenue did they generate

Step 3:
What is your current advertising budget

step 4:
Do you have a CRM and if so what is it

Step 5:
What is your personal informagtion
name
email
phone

Let me know if this is enough to get you going

Small and medium sized law firms, ecommerce, home services and lead gen customers.

We are a digital marketing agency

• Use whats on the current site and improve upon it

• Must be very secure, developed into a wordpress website. using gravity forms. remove my photo and my staffs photo, depersonalize it so it doesnt mention me or sam crolley. Use the same color scheme. I am looking to redesign the homepage, blog page and services page. The services page will be a template for all inner pages of the site. All content needs to be moved into the new design. I want to get ride of the weird video. I need you to install gravity forms pro model so we can pass utms. I need the gravity form to be a multi step form with icons. All "contact us" or "get a free assesments" call to actions will go to this form only. step 1: what is your website step 2: what industry are you in - option - Home Services - Legal - Ecommerce - Lead Gen No matter which one they select its going to produce a differnt calculator for them. Law: How many leads did you get last month how much is each ase worth on average How much revenue do you want to make Home servicse: How many bookings did you get last month How much is each service worht on average How much revenue do you wangt to make Ecommerce: What is your average order value How muny purchases did you have last month How much revenue did you drive How much revenue do you want to drive For lead gen: How many leads did you get lawt month How much revenue did they generate How much revenue do you want to make Step 3: What is your current advertising budget step 4: Do you have a CRM and if so what is it Step 5: What is your personal informagtion name email phone Let me know if this is enough to get you going
• SHOULD NOT BE SLOPPY, I AM LOOKING FOR ATTENTION TO DETAIL.

```html
<!DOCTYPE html>
<html lang="en">
<head>
<meta charset="utf-8">
<title>Tall Pine Growth Marketing – Free Assessment</title>
<link href="https://fonts.googleapis.com/css2?family=Poppins:wght@300;400;500;600;700;800&display=swap" rel="stylesheet">
<style>
  :root{
    --maroon:#6e1418;
    --maroon-deep:#5a0f12;
    --orange:#f7941d;
    --ink:#333333;
    --ink-soft:#4a4a4a;
    --grey:#8a8a8a;
    --line:#bdbdbd;
    --rule:#e2e2e2;
    --nav:#2d2d2d;
    --white:#ffffff;
  }
  *{box-sizing:border-box;margin:0;padding:0}
  html,body{width:916px;height:1200px;overflow:hidden;background:var(--white)}
  body{position:relative;font-family:'Poppins',sans-serif;color:var(--ink)}
  .abs{position:absolute}

  /* header */
  .brand{display:flex;align-items:center;gap:12px}
  .brand-mark{width:46px;height:46px;border-radius:50%;background:var(--maroon);flex:none}
  .brand-name{font-size:18px;font-weight:400;letter-spacing:1.6px;color:var(--ink-soft);line-height:1}
  .brand-tag{font-size:7px;letter-spacing:3.4px;color:var(--ink-soft);margin-top:6px;line-height:1}
  .call{left:431px;top:25px;font-size:13.5px;font-weight:600;color:var(--ink-soft)}
  .call b{color:var(--maroon);font-weight:700}
  .btn-orange{background:var(--orange);color:var(--white);font-weight:600;display:flex;align-items:center;justify-content:center}
  .header-cta{left:689px;top:16px;width:171px;height:37px;font-size:11px;letter-spacing:.4px}

  .nav{left:0;top:69px;width:916px;height:42px;background:var(--nav);display:flex;align-items:center;justify-content:center;gap:36px}
  .nav a{color:var(--white);text-decoration:none;font-size:10.5px;letter-spacing:.3px}

  /* assessment */
  .section-title{left:0;width:916px;text-align:center;font-size:28px;font-weight:800;color:var(--ink);letter-spacing:.3px}
  .title-rule{left:423px;width:71px;height:2px;background:var(--maroon)}

  .progress-line{top:253px;height:1.5px;background:var(--line)}
  .progress-line.active{background:var(--maroon)}
  .step-dot{top:231.5px;width:44px;height:44px;border-radius:50%;border:1.5px solid var(--grey);background:var(--white);
    display:flex;align-items:center;justify-content:center;font-size:17px;font-weight:700;color:var(--grey)}
  .step-dot.active{border-color:var(--maroon);color:var(--maroon)}

  .step-icon{left:223px;top:318px;width:33px;height:33px}
  .step-label{left:266px;top:313px;font-size:14.5px;font-weight:700;color:var(--maroon)}
  .step-question{left:266px;top:336px;font-size:12px;font-weight:500;color:var(--ink)}
  .field{left:223.5px;top:366.5px;width:377px;height:38px;border:1px solid #c9c9c9;display:flex;align-items:center;padding-left:14px;font-size:9.5px;color:var(--ink)}
  .next{left:607.5px;top:366.5px;width:88px;height:38px;background:var(--nav);color:var(--white);font-size:14.5px;font-weight:700;display:flex;align-items:center;justify-content:center;gap:9px}

  /* band */
  .band{left:0;top:462px;width:916px;height:245px;background:linear-gradient(100deg,#6a1215 0%,#7a181b 45%,#5e1013 100%)}
  .band-title{left:0;top:519px;width:916px;text-align:center;font-size:28px;font-weight:800;color:var(--white);letter-spacing:.3px}
  .band-rule{left:423px;top:567px;width:71px;height:2px;background:var(--white)}
  .band-cta{left:354px;top:603px;width:208px;height:43px;font-size:13.5px;letter-spacing:.2px}

  /* footer badges */
  .partner-badge{left:317px;top:743px;width:158px;height:67px;display:flex;gap:14px}
  .partner-badge .strip{width:18px;height:67px;background:#e4402f}
  .partner-badge .plate{flex:1;height:67px;background:#eeeeee}
  .listing-badge{left:524px;top:743px;width:67px;height:67px;border-radius:50%;background:#173a5e}
  .follow{left:675px;top:746px;font-size:12.5px;font-weight:500;letter-spacing:.6px;color:var(--ink-soft)}
  .social{top:780px;width:22px;height:22px;border-radius:50%;background:var(--ink-soft)}
  .footer-rule{left:0;width:916px;height:1px;background:var(--rule)}

  .col{top:864px}
  .col h3{font-size:18px;font-weight:700;color:#3a3a3a;letter-spacing:.3px;line-height:1;margin-bottom:11px}
  .col ul{list-style:none}
  .col li{font-size:10px;letter-spacing:.35px;color:var(--ink-soft);height:25px;line-height:16px}
  .col.guides li{height:auto;line-height:16.5px;margin-bottom:9px}
  .copyright{left:0;top:1158px;width:916px;text-align:center;font-size:10px;letter-spacing:.2px;color:var(--ink-soft)}
</style>
</head>
<body>

<!-- header -->
<div class="abs brand" style="left:58px;top:10px">
  <span class="brand-mark"></span>
  <div>
    <div class="brand-name">TALL PINE</div>
    <div class="brand-tag">GROWTH MARKETING</div>
  </div>
</div>
<div class="abs call">OR CALL US NOW : <b>(480) 555-0142</b></div>
<div class="abs btn-orange header-cta">GROW YOUR REVENUE</div>

<nav class="abs nav">
  <a>HOME</a><a>ABOUT</a><a>INDUSTRIES</a><a>SERVICES</a><a>RESOURCES</a><a>TRAINING</a><a>BLOG</a><a>CONTACT US</a>
</nav>

<!-- assessment form -->
<h1 class="abs section-title" style="top:148px">GET A FREE ASSESSMENTS</h1>
<div class="abs title-rule" style="top:195.5px"></div>

<div class="abs progress-line" style="left:252px;width:435px"></div>
<div class="abs progress-line active" style="left:252px;width:57px"></div>
<div class="abs step-dot active" style="left:208px">1</div>
<div class="abs step-dot" style="left:322px">2</div>
<div class="abs step-dot" style="left:437px">3</div>
<div class="abs step-dot" style="left:551px">4</div>
<div class="abs step-dot" style="left:665px">5</div>

<svg class="abs step-icon" viewBox="0 0 33 33" fill="none" stroke="#6e1418" stroke-width="1">
  <circle cx="16.5" cy="16.5" r="15.5"/>
  <ellipse cx="16.5" cy="16.5" rx="7" ry="15.5"/>
  <line x1="16.5" y1="1" x2="16.5" y2="32"/>
  <path d="M3 9h27M3 24h27"/>
  <rect x="1" y="12.5" width="31" height="8" fill="#fff"/>
  <text x="16.5" y="19" text-anchor="middle" font-family="Poppins,sans-serif" font-size="6.5" fill="#6e1418" stroke="none">www.</text>
</svg>
<div class="abs step-label">Step 1</div>
<div class="abs step-question">What is your website</div>
<div class="abs field">Enter business name</div>
<div class="abs next">NEXT
  <svg width="7" height="12" viewBox="0 0 7 12" fill="none" stroke="#fff" stroke-width="1.4"><path d="M1 1l5 5-5 5"/></svg>
</div>

<!-- band -->
<div class="abs band" role="img" aria-label="Hands pointing at a laptop showing marketing charts, tinted deep red"></div>
<h2 class="abs band-title">ELEVATE YOUR MARKETING</h2>
<div class="abs band-rule"></div>
<div class="abs btn-orange band-cta">Grow Your Revenue</div>

<!-- footer badges -->
<div class="abs brand" style="left:57px;top:753px">
  <span class="brand-mark"></span>
  <div>
    <div class="brand-name">TALL PINE</div>
    <div class="brand-tag">GROWTH MARKETING</div>
  </div>
</div>
<div class="abs partner-badge" role="img" aria-label="Advertising partner badge"><span class="strip"></span><span class="plate"></span></div>
<div class="abs listing-badge" role="img" aria-label="Client review listing badge"></div>
<div class="abs follow">FOLLOW US</div>
<span class="abs social" style="left:672px" aria-label="Social profile"></span>
<span class="abs social" style="left:710px" aria-label="Social profile"></span>
<span class="abs social" style="left:748px" aria-label="Social profile"></span>
<span class="abs social" style="left:792px" aria-label="Social profile"></span>
<span class="abs social" style="left:837px" aria-label="Social profile"></span>

<div class="abs footer-rule" style="top:834px"></div>

<div class="abs col" style="left:57px">
  <h3>QUICK LINKS</h3>
  <ul><li>About</li><li>Industries</li><li>Services</li><li>Resources</li><li>Training</li><li>Blog</li><li>Contact Us</li></ul>
</div>
<div class="abs col" style="left:243px">
  <h3>SERVICES</h3>
  <ul><li>Programmatic Advertising</li><li>Search Engine Marketing (SEM)</li><li>Search Engine Optimization (SEO)</li><li>Content Marketing</li><li>Email Marketing</li><li>Paid Search Advertising</li><li>Paid Social Advertising</li></ul>
</div>
<div class="abs col" style="left:470px">
  <h3>INDUSTRIES</h3>
  <ul><li>Ecommerce</li><li>Electricians</li><li>Financial Services Marketing</li><li>Home Builders</li><li>Home Services</li><li>Hvac Companies</li><li>Cosmetic Surgery Centers</li><li>Dental Marketing</li></ul>
</div>
<div class="abs col guides" style="left:675px;width:182px">
  <h3>GUIDES</h3>
  <ul>
    <li>Ultimate Guide On Growing Your Medical Practice Business</li>
    <li>Legal Marketing Strategy Guide For Law Firm Offices</li>
    <li>Ultimate Short Video Ads Guide To Skyrocket Your Leads And Sales</li>
    <li>Ultimate Guide To Search<br>Engine Queries</li>
  </ul>
</div>

<div class="abs footer-rule" style="top:1135px"></div>
<p class="abs copyright">Copyright © 2024 CompanyName&nbsp; All Rights Reserved. Privacy Policy, Terms Of Use, Press &amp; Media, Cookie Policy</p>

</body>
</html>
```